Thornvale Group needs a business card design

We need a new business card design using the logo recently selected in a logo competition on Pixel Bazaar. Our business is a consultancy specializing in aviation and energy and the winning business card design will promote an image of precision and professionalism with creativity.

Please use the logo with the name on the front of the card and use a complementary font. Make the back white with either the light grey or dark grey logo.

Target Market(s)

Senior finance and legal leaders at aviation and energy companies

Industry/Entity Type

Management Consulting

Contact Information for Business Card

Peter Castrell
President
Thornvale Group

www.thornvalegroup.example

(555) 204-6391
pc@thornvalegroup.example

Requirements
Must have
• Professional font that goes well with the logo font

```html
<!DOCTYPE html>
<html lang="en">
<head>
<meta charset="utf-8">
<title>Thornvale Group – Business Card</title>
<link rel="stylesheet" href="https://fonts.googleapis.com/css2?family=Arimo:wght@400;700&display=swap">
<style>
  :root {
    --backdrop: #4b4541;
    --card: #1c1c1e;
    --card-edge: #2a2a2d;
    --brand-blue: #24508f;
    --text-light: #eef0f3;
    --text-muted: #6f7074;
    --divider: #5a5b60;
  }
  * { margin: 0; padding: 0; box-sizing: border-box; }
  html, body {
    width: 1200px; height: 787px; overflow: hidden;
    background: var(--backdrop);
    font-family: "Arimo", Arial, sans-serif;
  }
  .stage {
    position: relative; width: 1200px; height: 787px;
    display: flex; align-items: center; justify-content: center; gap: 40px;
  }
  .card {
    position: relative; width: 540px; height: 309px;
    background: var(--card);
    border: 1px solid var(--card-edge);
    box-shadow: 0 10px 30px rgba(0,0,0,.35);
  }

  /* Back of card */
  .card-back .brand-name {
    position: absolute; left: 60px; top: 100px;
    display: flex; align-items: center; gap: 14px;
    color: var(--brand-blue); font-weight: 700; font-size: 38px;
    letter-spacing: 1px;
  }
  .brand-mark { width: 26px; height: 26px; background: var(--brand-blue); }
  .card-back .website {
    position: absolute; left: 62px; top: 200px;
    color: var(--text-light); font-size: 15px; letter-spacing: 3px;
  }

  /* Front of card */
  .card-front .brand-block {
    position: absolute; left: 34px; top: 0; bottom: 0; width: 220px;
    display: flex; flex-direction: column; align-items: center; justify-content: center; gap: 14px;
  }
  .card-front .brand-mark { width: 30px; height: 30px; }
  .card-front .brand-name {
    color: var(--brand-blue); font-weight: 700; font-size: 26px;
    letter-spacing: 1px; text-align: center; line-height: 1.1;
  }
  .divider {
    position: absolute; left: 272px; top: 36px; bottom: 36px; width: 1px;
    background: linear-gradient(var(--card), var(--divider) 30%, var(--divider) 70%, var(--card));
  }
  .contact {
    position: absolute; left: 296px; top: 44px; right: 20px;
    color: var(--text-light); font-size: 14px; line-height: 1.35;
  }
  .person-name { color: var(--brand-blue); font-weight: 700; font-size: 19px; }
  .person-title { color: var(--text-muted); font-size: 15px; margin-bottom: 16px; }
  .company-lines { margin-bottom: 8px; }
  .contact-row { display: flex; align-items: center; gap: 8px; }
  .contact-row svg { width: 13px; height: 13px; flex: none; fill: var(--brand-blue); }
</style>
</head>
<body>
<main class="stage">
  <section class="card card-back" aria-label="Card back">
    <div class="brand-name"><span class="brand-mark"></span>Thornvale Group</div>
    <div class="website">www.thornvalegroup.example</div>
  </section>

  <section class="card card-front" aria-label="Card front">
    <div class="brand-block">
      <span class="brand-mark"></span>
      <div class="brand-name">Thornvale Group</div>
    </div>
    <div class="divider"></div>
    <div class="contact">
      <div class="person-name">Peter J. Castrell</div>
      <div class="person-title">President</div>
      <div class="company-lines">
        Thornvale Group LLC<br>
        Finance and Strategy Consulting<br>
        Aviation - Manufacturing - Energy
      </div>
      <div class="contact-row">
        <svg viewBox="0 0 16 16" aria-hidden="true"><path d="M3 1h3l1.5 4-2 1.2a9 9 0 0 0 4.3 4.3L11 8.5 15 10v3a2 2 0 0 1-2 2A12 12 0 0 1 1 3a2 2 0 0 1 2-2z"/></svg>
        (555) 204-6391
      </div>
      <div class="contact-row">
        <svg viewBox="0 0 16 16" aria-hidden="true"><path d="M1 3h14v10H1z M1 3l7 6 7-6" fill="none" stroke="#24508f" stroke-width="1.8"/></svg>
        pc@thornvalegroup.example
      </div>
      <div class="contact-row">
        <svg viewBox="0 0 16 16" aria-hidden="true"><circle cx="8" cy="8" r="6.5" fill="none" stroke="#24508f" stroke-width="1.6"/><path d="M1.5 8h13M8 1.5c-3 3.5-3 9.5 0 13M8 1.5c3 3.5 3 9.5 0 13" fill="none" stroke="#24508f" stroke-width="1.2"/></svg>
        thornvalegroup.example
      </div>
    </div>
  </section>
</main>
</body>
</html>
```